use my brand and make an elegant business card  with it

Target Market(s)
male and female ' ages 25 to 45 age- who appreciate the highest quality goods, experiences, services, brands and relationships
Industry/Entity Type
Business
Requirements
Must have
- my logo integrated into the design-note the uploaded file
front: just logo and the phrase: New. Trend. Life. Style
back informations:
Maren Tosvik
Director
phone: +1 604 2957318
www.matosvik.com
email: marentosvik@matosvik.com
the pin of Facebook (F) and tweeter (T)
Nice to have
- contrast of the colors black gold and silver
Should not have
- cartoons or whimsical design

```html
<!DOCTYPE html>
<html lang="en">
<head>
<meta charset="UTF-8">
<title>Maren Tosvik — Business Card</title>
<link href="https://fonts.googleapis.com/css2?family=Old+Standard+TT:wght@400;700&family=Montserrat:wght@500;600&display=swap" rel="stylesheet">
<style>
  :root {
    --card-black: #0b0b0b;
    --card-charcoal: #1c1c1e;
    --gold: #c28f0e;
    --silver: #8c8c8c;
    --silver-light: #a6a6a6;
    --silver-dark: #6f6f6f;
  }
  html, body {
    margin: 0;
    padding: 0;
    width: 1200px;
    height: 720px;
    overflow: hidden;
    background: var(--card-black);
  }
  .card {
    position: relative;
    width: 1200px;
    height: 720px;
    overflow: hidden;
    font-family: "Old Standard TT", Georgia, serif;
  }
  .card__leather {
    position: absolute;
    inset: 0;
    background: radial-gradient(ellipse at 50% 40%, var(--card-charcoal) 0%, #121213 55%, var(--card-black) 100%);
  }
  .tagline {
    position: absolute;
    top: 66px;
    left: 0;
    width: 1216px;
    margin: 0;
    text-align: center;
    font-family: "Montserrat", Arial, sans-serif;
    font-weight: 500;
    font-variant: small-caps;
    font-size: 34px;
    letter-spacing: 4px;
    color: var(--silver-light);
    line-height: 1;
  }
  .divider {
    position: absolute;
    left: 595px;
    top: 109px;
    width: 9px;
    height: 518px;
    background: var(--gold);
  }
  .identity {
    position: absolute;
    left: 139px;
    width: 400px;
    text-align: center;
  }
  .identity__name {
    position: absolute;
    top: 268px;
    left: 0;
    width: 100%;
    margin: 0;
    font-size: 54px;
    font-weight: 400;
    color: var(--gold);
    line-height: 1;
  }
  .identity__role {
    position: absolute;
    top: 367px;
    left: 0;
    width: 100%;
    margin: 0;
    font-family: "Montserrat", Arial, sans-serif;
    font-weight: 600;
    font-size: 32px;
    letter-spacing: 1px;
    color: var(--silver-dark);
    line-height: 1;
  }
  .contact {
    position: absolute;
    left: 648px;
    display: flex;
    align-items: center;
    gap: 24px;
    color: var(--silver);
    line-height: 1;
  }
  .contact__icon { width: 52px; height: 52px; flex: none; }
  .contact--phone { top: 306px; font-size: 49px; letter-spacing: 2px; }
  .contact--email { top: 370px; font-size: 25px; text-transform: uppercase; }
  .web {
    position: absolute;
    left: 39px;
    top: 599px;
  }
  .web__corner { position: absolute; left: 0; top: 0; }
  .web__address {
    position: absolute;
    left: 68px;
    top: 50px;
    margin: 0;
    font-size: 35px;
    text-transform: uppercase;
    color: var(--silver-dark);
    white-space: nowrap;
    line-height: 1;
  }
  .web__domain { color: var(--gold); }
  .social {
    position: absolute;
    left: 678px;
    top: 619px;
    display: flex;
    gap: 12px;
  }
  .social__pin {
    width: 40px;
    height: 40px;
    display: block;
  }
  .brand-name {
    position: absolute;
    left: 804px;
    top: 618px;
    margin: 0;
    font-size: 46px;
    font-weight: 400;
    color: var(--silver-light);
    line-height: 1;
    white-space: nowrap;
  }
</style>
</head>
<body>
  <main class="card">
    <div class="card__leather" role="img" aria-label="Black leather texture background"></div>

    <p class="tagline">New. Trend. Life. Style</p>

    <div class="divider"></div>

    <section class="identity">
      <h1 class="identity__name">Maren Tosvik</h1>
      <p class="identity__role">DIRECTOR</p>
    </section>

    <div class="contact contact--phone">
      <svg class="contact__icon" viewBox="0 0 52 52" aria-hidden="true">
        <circle cx="26" cy="26" r="23" fill="none" stroke="var(--gold)" stroke-width="2.5"/>
        <path d="M19 14 h5 l2 7 -3 2.5 c1.5 3.5 3.5 5.5 7 7 l2.5 -3 7 2 v5 c0 1.5 -1 2.5 -2.5 2.5 C25 37 15 27 15 16.5 15 15 16 14 17.5 14 Z" fill="var(--gold)"/>
      </svg>
      <span>+1 604 2957318</span>
    </div>

    <div class="contact contact--email">
      <svg class="contact__icon" viewBox="0 0 52 52" aria-hidden="true">
        <circle cx="26" cy="26" r="23" fill="none" stroke="var(--gold)" stroke-width="2.5"/>
        <rect x="13" y="17" width="26" height="18" fill="var(--gold)"/>
        <path d="M13 17 L26 28 L39 17" fill="none" stroke="var(--card-black)" stroke-width="2"/>
      </svg>
      <span>marentosvik@matosvik.com</span>
    </div>

    <div class="web">
      <svg class="web__corner" width="60" height="82" viewBox="0 0 60 82" aria-hidden="true">
        <defs>
          <linearGradient id="cornerShade" x1="0" y1="0" x2="1" y2="1">
            <stop offset="0" stop-color="#9a9a9a"/>
            <stop offset="1" stop-color="#5e5e5e"/>
          </linearGradient>
        </defs>
        <polygon points="0,0 0,82 60,82" fill="url(#cornerShade)"/>
      </svg>
      <p class="web__address">www.<span class="web__domain">matosvik</span>.com</p>
    </div>

    <div class="social" aria-label="Social profiles">
      <svg class="social__pin" viewBox="0 0 40 40" role="img" aria-label="Social profile (chat)">
        <circle cx="20" cy="20" r="20" fill="var(--gold)"/>
        <path d="M11 13 h18 a2 2 0 0 1 2 2 v9 a2 2 0 0 1 -2 2 h-10 l-5 4 v-4 h-3 a2 2 0 0 1 -2 -2 v-9 a2 2 0 0 1 2 -2 Z" fill="var(--card-black)"/>
      </svg>
      <svg class="social__pin" viewBox="0 0 40 40" role="img" aria-label="Social profile (link)">
        <circle cx="20" cy="20" r="20" fill="var(--gold)"/>
        <g fill="none" stroke="var(--card-black)" stroke-width="3" stroke-linecap="round">
          <path d="M18 22 l-3 3 a4 4 0 0 1 -5.6 -5.6 l3 -3 a4 4 0 0 1 5.6 0"/>
          <path d="M22 18 l3 -3 a4 4 0 0 1 5.6 5.6 l-3 3 a4 4 0 0 1 -5.6 0"/>
          <path d="M17 23 l6 -6"/>
        </g>
      </svg>
    </div>

    <p class="brand-name">Ma Tosvik</p>
  </main>
</body>
</html>
```